Super elegant, crisp & clean Business card design required

We recently upgraded our branding - which is on our website - talvendoraphoto.com

I would like a simple, yet elegant, clean business card design please.

The font of my logo is Cinzel - and because of the natural colour - it's best to have this on a black background.

I would like to have the back of the business card - with simply my logo.

PLEASE DO NOT SUBMIT A COMPLICATED / UNCLEAN DESIGN

Industry/Entity Type

Business

Contact Information for Business Card

Talven Doroshko Photography

Font styles to use
Other font styles liked:
• Cinzel

Requirements
Must have
• A backpage with nothing but my logo
• Simple design - stands out
Should not have
• Colour that dont align with my logo
• Over complicated '/ non symmetrical design

```html
<!DOCTYPE html>
<html lang="en">
<head>
<meta charset="utf-8">
<title>Talven Doroshko Photography – Business Card</title>
<link rel="stylesheet" href="https://fonts.googleapis.com/css2?family=Cinzel:wght@400&family=Montserrat:wght@300&display=swap">
<style>
  :root {
    --page: #ece9e3;
    --dark-1: #433e38;
    --dark-2: #625b52;
    --light-1: #a59d86;
    --light-2: #cbc4ae;
    --ink: #ffffff;
    --ink-soft: rgba(255,255,255,0.82);
  }
  * { margin: 0; padding: 0; box-sizing: border-box; }
  html, body {
    width: 1200px; height: 858px; overflow: hidden;
    background: var(--page);
  }
  .sheet {
    position: relative; width: 1200px; height: 858px;
    display: flex; align-items: center; justify-content: center; gap: 40px;
  }
  .card {
    position: relative; width: 540px; height: 309px;
    overflow: hidden; border-radius: 3px;
    box-shadow: 0 6px 18px rgba(0,0,0,0.18);
  }
  .card-front { background: linear-gradient(135deg, var(--light-1), var(--light-2)); }
  .card-back { background: radial-gradient(ellipse at 45% 40%, var(--light-2), var(--light-1)); }
  .card-shape { position: absolute; inset: 0; }

  .brand {
    position: absolute; display: flex; flex-direction: column; align-items: center;
    font-family: "Cinzel", serif; font-weight: 400; color: var(--ink);
    text-align: center; letter-spacing: 1px;
  }
  .brand-mark {
    width: 46px; height: 46px; border: 1.5px solid var(--ink); border-radius: 50%;
    margin-bottom: 14px;
  }
  .brand-name { font-size: 17px; line-height: 1.2; }
  .brand-sub { font-size: 17px; letter-spacing: 6px; line-height: 1.4; }
  .card-front .brand { left: 20px; top: 92px; width: 190px; }
  .card-front .brand-name, .card-front .brand-sub { font-size: 15px; }
  .card-front .brand-sub { letter-spacing: 5px; }
  .card-back .brand { left: 0; right: 0; top: 88px; }
  .card-back .brand-name { font-size: 22px; letter-spacing: 2px; }
  .card-back .brand-sub { font-size: 22px; letter-spacing: 8px; }

  .holder {
    position: absolute; left: 300px; top: 58px;
    font-family: "Cinzel", serif; color: var(--ink);
  }
  .holder-name { font-size: 20px; letter-spacing: 1px; }
  .holder-role { font-size: 11px; letter-spacing: 2px; color: var(--ink-soft); margin-top: 4px; }

  .contacts {
    position: absolute; left: 300px; top: 192px; list-style: none;
    font-family: "Montserrat", sans-serif; font-weight: 300;
    font-size: 12.5px; color: var(--ink); letter-spacing: 0.3px;
  }
  .contacts li { display: flex; align-items: center; gap: 10px; height: 22px; }
  .contact-icon { width: 13px; height: 13px; flex: none; }
</style>
</head>
<body>
<main class="sheet">

  <section class="card card-front" aria-label="Card front">
    <svg class="card-shape" viewBox="0 0 540 309" aria-hidden="true">
      <defs>
        <linearGradient id="darkPanel" x1="0" y1="0" x2="1" y2="1">
          <stop offset="0" stop-color="#433e38"/>
          <stop offset="0.55" stop-color="#625b52"/>
          <stop offset="1" stop-color="#4a443d"/>
        </linearGradient>
      </defs>
      <path d="M258 0 Q196 154 258 309 L540 309 L540 0 Z" fill="url(#darkPanel)"/>
      <path d="M250 0 Q188 154 250 309" fill="none" stroke="#ffffff" stroke-width="3"/>
    </svg>

    <div class="brand">
      <span class="brand-mark"></span>
      <span class="brand-name">Talven Doroshko</span>
      <span class="brand-sub">Photography</span>
    </div>

    <div class="holder">
      <div class="holder-name">Talven Doroshko</div>
      <div class="holder-role">OWNER</div>
    </div>

    <ul class="contacts">
      <li>
        <svg class="contact-icon" viewBox="0 0 13 13" aria-hidden="true"><rect width="13" height="13" rx="1.5" fill="#fff"/><path d="M4 3 L5.5 3 L6 5 L5 5.8 Q6 7.6 7.2 8 L8 7 L10 7.5 L10 9 Q6 10 3.5 4.5 Z" fill="#4a443d"/></svg>
        <span>07700914362</span>
      </li>
      <li>
        <svg class="contact-icon" viewBox="0 0 13 13" aria-hidden="true"><rect width="13" height="13" rx="1.5" fill="#fff"/><circle cx="6.5" cy="6.5" r="3.6" fill="none" stroke="#4a443d" stroke-width="0.9"/><path d="M2.9 6.5 H10.1 M6.5 2.9 Q4.5 6.5 6.5 10.1 Q8.5 6.5 6.5 2.9" fill="none" stroke="#4a443d" stroke-width="0.8"/></svg>
        <span>www.talvendoraphoto.com</span>
      </li>
      <li>
        <svg class="contact-icon" viewBox="0 0 13 13" aria-hidden="true"><rect width="13" height="13" rx="1.5" fill="#fff"/><rect x="2.8" y="4" width="7.4" height="5.2" fill="none" stroke="#4a443d" stroke-width="0.9"/><path d="M2.8 4 L6.5 7 L10.2 4" fill="none" stroke="#4a443d" stroke-width="0.9"/></svg>
        <span>info@talvendoraphoto.com</span>
      </li>
    </ul>
  </section>

  <section class="card card-back" aria-label="Card back">
    <div class="brand">
      <span class="brand-mark"></span>
      <span class="brand-name">Talven Doroshko</span>
      <span class="brand-sub">Photography</span>
    </div>
  </section>

</main>
</body>
</html>
```